Journal Cover Design Project

The Worldwide Review of Rising Trade Systems is a professional journal which aims to provide an international platform for publication of original research on the emerging economies.
The journal is published three times a year and available by subscription. Currently, the cover design is the same for each issue. We are looking to redesign the cover (and interior) of our journal and would like a design that would allow us to change the color scheme for each issue or volume while maintaining a consistent design scheme.
Our design preference is simple and modern with good use of color. Many of our past publications have used abstract maps/globes but we are open to new ideas. We would need a creative way to include text on the cover, possibly a way to present the article titles or main topics for each issue. For example, we like the use of color and the general design in this image: http://www.pictavo.example/photos/moonlitpaperkite/5120448391/lightbox/
Below is a link to our most recent issue of the journal. You can see an example of the article titles, structure, etc. The website also shows the current cover of the journal (but we do not want the new design to be based off of the current one):
http://wrt.plovarhouse.example/content/4/2.toc

```html
<!DOCTYPE html>
<html lang="en">
<head>
<meta charset="utf-8">
<title>The Worldwide Review of Rising Trade Systems – Volume 5 Issue 1</title>
<link rel="stylesheet" href="https://fonts.googleapis.com/css2?family=Roboto+Condensed:wght@400;700&display=swap">
<style>
  :root {
    --page-bg: #ffffff;
    --cover-white: #ffffff;
    --band-green: #8dbd4c;
    --field-green: #c6dc9a;
    --field-green-light: #d3e4ae;
    --ink: #1b1b1b;
    --title-white: #ffffff;
    --globe-line: #d9d9d9;
  }
  * { margin: 0; padding: 0; box-sizing: border-box; }
  html, body {
    width: 1001px;
    height: 1200px;
    overflow: hidden;
    background: var(--page-bg);
  }
  body {
    position: relative;
    font-family: "Roboto Condensed", "Arial Narrow", sans-serif;
    color: var(--ink);
  }
  .cover {
    position: absolute;
    left: 71px;
    top: 30px;
    width: 859px;
    height: 1127px;
    background: var(--cover-white);
    overflow: hidden;
  }
  .issue-label {
    position: absolute;
    left: 79px;
    top: 112px;
    font-size: 20px;
    font-weight: 700;
    letter-spacing: 0.2px;
  }
  .globe-art {
    position: absolute;
    left: 300px;
    top: 48px;
    width: 559px;
    height: 248px;
    border-radius: 280px 280px 0 0 / 240px 240px 0 0;
    background: radial-gradient(ellipse at 55% 100%, #f3f3f3 0%, #e8e8e8 60%, var(--globe-line) 100%);
  }
  .title-band {
    position: absolute;
    left: 0;
    top: 296px;
    width: 100%;
    height: 188px;
    background: var(--band-green);
  }
  .journal-title {
    position: absolute;
    left: 79px;
    top: 300px;
    color: var(--title-white);
    font-weight: 700;
    line-height: 1;
  }
  .journal-title .main {
    display: block;
    font-size: 76px;
    letter-spacing: -0.5px;
  }
  .journal-title .sub {
    display: block;
    font-size: 45px;
    margin-top: 6px;
  }
  .contents-field {
    position: absolute;
    left: 0;
    top: 484px;
    width: 100%;
    height: 643px;
    background: linear-gradient(180deg, var(--field-green) 0%, var(--field-green-light) 55%, var(--field-green) 100%);
  }
  .article-list {
    position: absolute;
    left: 79px;
    top: 540px;
    list-style: none;
  }
  .article { margin-bottom: 26px; }
  .article:nth-child(2) { margin-bottom: 40px; }
  .article:nth-child(3) { margin-bottom: 46px; }
  .article-head {
    font-size: 30px;
    font-weight: 700;
    line-height: 1.1;
    letter-spacing: -0.2px;
  }
  .article-sub {
    font-size: 17px;
    font-weight: 700;
    line-height: 1.12;
    margin-top: 2px;
  }
  .issue-date {
    position: absolute;
    left: 66px;
    top: 990px;
    font-size: 66px;
    font-weight: 700;
    color: var(--title-white);
    letter-spacing: -0.5px;
  }
  .forum-mark {
    position: absolute;
    left: 548px;
    top: 985px;
    display: flex;
    align-items: center;
    gap: 10px;
  }
  .forum-mark .square {
    width: 46px;
    height: 46px;
    background: var(--ink);
  }
  .forum-mark .name {
    font-size: 19px;
    font-weight: 700;
    line-height: 1.05;
    color: var(--ink);
  }
  .publisher-mark {
    position: absolute;
    left: 790px;
    top: 990px;
    width: 42px;
    height: 42px;
    border-radius: 50%;
    background: var(--ink);
  }
</style>
</head>
<body>
  <main class="cover">
    <div class="issue-label">VOLUME 5 ISSUE 1</div>
    <div class="globe-art" role="img" aria-label="Wireframe globe of grey latitude and longitude lines"></div>

    <div class="title-band" role="img" aria-label="Green band with a fine grid pattern"></div>
    <h1 class="journal-title">
      <span class="main">Worldwide Review</span>
      <span class="sub">of Rising Trade Systems</span>
    </h1>

    <div class="contents-field" role="img" aria-label="Light green field with a flowing mesh of thin white curved lines"></div>

    <ul class="article-list">
      <li class="article">
        <div class="article-head">Construction and Analysis</div>
        <div class="article-sub">of a Global GDP Growth Model for<br>185 Countries through 2050</div>
      </li>
      <li class="article">
        <div class="article-head">A New Vision for Mexico 2042</div>
        <div class="article-sub">Achieving Prosperity for All</div>
      </li>
      <li class="article">
        <div class="article-head">India 2039</div>
        <div class="article-sub">Transforming Agriculture: Productivity,<br>Markets, and Institutions</div>
      </li>
      <li class="article">
        <div class="article-head">New Directions</div>
        <div class="article-sub">for Water Management in Indian Agriculture</div>
      </li>
    </ul>

    <div class="issue-date">08/2012</div>

    <div class="forum-mark">
      <span class="square"></span>
      <span class="name">Rising<br>Markets<br>Council</span>
    </div>
    <div class="publisher-mark" aria-hidden="true"></div>
  </main>
</body>
</html>
```